Business card update

Opening a subsidiary of my company in the USA and need to update my logo.
Updates

Reason: Give more time to a good design.

I made a mistake on my briefing. It's only the business card. Thanks for alerting me on the mistake.

All the best

Teodoro

Target Market(s)

We are an Executive Search company and our target audience are executives in large corporations.

Industry/Entity Type

Business

Requirements
Must have
• Keep the logo. In the US the company is called Delia Brunet Executive Search.

```html
<!DOCTYPE html>
<html lang="en">
<head>
<meta charset="utf-8">
<title>Delia Brunet Executive Search – Business Card</title>
<link rel="stylesheet" href="https://fonts.googleapis.com/css2?family=Quicksand:wght@400;500&display=swap">
<style>
  :root {
    --backdrop: #e4e7e8;
    --card: #ffffff;
    --teal: #3fcfa9;
    --teal-soft: #a6e9d6;
    --navy: #2d3b63;
    --ink: #2b2b2b;
    --ink-muted: #4a4a4a;
    --alert-red: #d8232a;
  }
  * { margin: 0; padding: 0; box-sizing: border-box; }
  html, body {
    width: 1200px;
    height: 741px;
    overflow: hidden;
    background: var(--backdrop);
    font-family: "Quicksand", sans-serif;
  }
  .card {
    position: absolute;
    left: 150px;
    top: 108px;
    width: 900px;
    height: 524px;
    background: var(--card);
    overflow: hidden;
  }
  .brand-name {
    position: absolute;
    right: 33px;
    top: 66px;
    font-size: 38px;
    font-weight: 500;
    letter-spacing: 5px;
    color: var(--navy);
    line-height: 1;
  }
  .holder-name {
    position: absolute;
    left: 43px;
    top: 166px;
    font-size: 38px;
    font-weight: 500;
    color: var(--teal);
    line-height: 1;
  }
  .holder-phone {
    position: absolute;
    left: 43px;
    top: 220px;
    display: flex;
    align-items: center;
    gap: 12px;
    font-size: 30px;
    font-weight: 500;
    color: var(--ink);
    line-height: 1;
  }
  .holder-phone svg { width: 22px; height: 26px; }
  .contact-list {
    position: absolute;
    left: 476px;
    top: 270px;
    list-style: none;
  }
  .contact-item {
    display: flex;
    align-items: flex-start;
    gap: 18px;
    font-size: 22px;
    color: var(--ink-muted);
    line-height: 31px;
    margin-bottom: 14px;
  }
  .contact-item svg { width: 24px; height: 24px; margin-top: 4px; flex: none; }
  .footer-band {
    position: absolute;
    left: 0;
    bottom: 0;
    width: 900px;
    height: 38px;
    display: flex;
    align-items: center;
  }
  .band-fill {
    height: 38px;
    background: var(--teal);
    opacity: .85;
  }
  .band-fill.left { width: 140px; }
  .band-fill.right { width: 164px; margin-left: auto; }
  .band-title {
    padding: 0 12px;
    font-size: 33px;
    color: var(--teal);
    letter-spacing: 1.5px;
    line-height: 1;
    white-space: nowrap;
  }
</style>
</head>
<body>
  <main class="card">
    <div class="brand-name">DELIA BRUNET</div>

    <h1 class="holder-name">Teodoro S. Brunet</h1>
    <p class="holder-phone">
      <svg viewBox="0 0 22 26" aria-hidden="true">
        <path d="M5 2 L9 2 L10 8 L7 10 C8 14 10 17 13 19 L16 16 L21 18 L20 23 C12 24 3 15 3 5 Z" fill="var(--alert-red)"/>
      </svg>
      305 555-0147
    </p>

    <ul class="contact-list">
      <li class="contact-item">
        <svg viewBox="0 0 24 24" aria-hidden="true">
          <rect x="2" y="5" width="20" height="14" fill="var(--teal-soft)"/>
          <path d="M2 5 L12 13 L22 5" fill="none" stroke="#fff" stroke-width="1.6"/>
        </svg>
        www.dbexecutivesearch.com
      </li>
      <li class="contact-item">
        <svg viewBox="0 0 24 24" aria-hidden="true">
          <circle cx="12" cy="12" r="10" fill="var(--teal-soft)"/>
          <path d="M2 12 H22 M12 2 C7 7 7 17 12 22 M12 2 C17 7 17 17 12 22" fill="none" stroke="#fff" stroke-width="1.4"/>
        </svg>
        tbrunet@dbexecutivesearch.com
      </li>
      <li class="contact-item">
        <svg viewBox="0 0 24 24" aria-hidden="true">
          <path d="M12 2 L23 12 H20 V22 H4 V12 H1 Z" fill="var(--teal-soft)"/>
          <rect x="10" y="15" width="4" height="7" fill="#fff"/>
        </svg>
        <span>4820 Harbor Point Ave Suite 310<br>Coral Bay FL 33140</span>
      </li>
    </ul>

    <footer class="footer-band">
      <div class="band-fill left" role="img" aria-label="Decorative striped teal band"></div>
      <span class="band-title">Delia Brunet Executive Search</span>
      <div class="band-fill right" role="img" aria-label="Decorative striped teal band"></div>
    </footer>
  </main>
</body>
</html>
```